Business card for law firm

Need business card for new law firm. Think confident, authoritative, conservative, but not stuffy or old-fashioned.

Contact Information for Business Card

Content for card - logo (uploaded), plus the following:

Paul Whitcombe (larger font)
Managing Partner (larger font, but not as large as name)
Level 9, 7 Ferris Lane
Sydney NSW 2000
Main Tel 02 9364 2710
Direct Tel 02 8472 3159
Email paul@qvlegal.com.au
www.qvlegal.com.au

Letterhead design should include logo plus:
Level 9, 7 Ferris Lane
Sydney NSW 2000
Tel 02 8472 3159
www.qvlegal.com.au

```html
<!DOCTYPE html>
<html lang="en">
<head>
<meta charset="utf-8">
<title>Quayvale Legal – Letterhead</title>
<link rel="stylesheet" href="https://fonts.googleapis.com/css2?family=Questrial&family=Libre+Baskerville&display=swap">
<style>
  :root {
    --backdrop: #e4e4e6;
    --paper: #f3f3f4;
    --navy: #1c2a5e;
    --body-text: #5a5a5f;
    --signature-ink: #4a7fcf;
  }
  * { margin: 0; padding: 0; box-sizing: border-box; }
  html, body {
    width: 1024px;
    height: 1200px;
    overflow: hidden;
    background: var(--backdrop);
  }
  .letterhead {
    position: absolute;
    left: 110px;
    top: 35px;
    width: 805px;
    height: 1130px;
    background: var(--paper);
    box-shadow: 0 6px 24px rgba(0, 0, 0, 0.12);
  }
  .brand {
    position: absolute;
    left: 71px;
    top: 69px;
    width: 155px;
    text-align: center;
    color: var(--navy);
    font-family: "Libre Baskerville", Georgia, serif;
  }
  .brand-square {
    display: block;
    width: 36px;
    height: 36px;
    margin: 0 auto 14px;
    background: var(--navy);
  }
  .brand-name {
    display: block;
    font-size: 20px;
    letter-spacing: 1px;
    line-height: 1;
  }
  .brand-sub {
    display: block;
    font-size: 8px;
    letter-spacing: 7px;
    margin-top: 6px;
    padding-left: 7px;
  }
  .contact {
    position: absolute;
    right: 65px;
    top: 78px;
    text-align: right;
    color: var(--navy);
    font-family: "Libre Baskerville", Georgia, serif;
    font-size: 14px;
    line-height: 17px;
    font-style: normal;
  }
  .contact .phone { margin-top: 6px; }
  .salutation {
    position: absolute;
    left: 75px;
    top: 300px;
    font-family: "Questrial", "Century Gothic", sans-serif;
    font-size: 20px;
    color: var(--body-text);
  }
  .letter-body {
    position: absolute;
    left: 75px;
    top: 357px;
    width: 665px;
    font-family: "Questrial", "Century Gothic", sans-serif;
    font-size: 11.2px;
    line-height: 15px;
    color: var(--body-text);
    text-align: justify;
    hyphens: auto;
  }
  .letter-body p + p { margin-top: 15px; }
  .closing {
    position: absolute;
    left: 75px;
    top: 716px;
    font-family: "Questrial", "Century Gothic", sans-serif;
    font-size: 11.2px;
    color: var(--body-text);
  }
  .signature {
    position: absolute;
    left: 72px;
    top: 780px;
    width: 140px;
    height: 70px;
    border-radius: 6px;
    background: linear-gradient(135deg, rgba(74, 127, 207, 0.25), rgba(74, 127, 207, 0.12));
  }
</style>
</head>
<body>
  <main class="letterhead">
    <header>
      <div class="brand">
        <span class="brand-square"></span>
        <span class="brand-name">QUAYVALE</span>
        <span class="brand-sub">LEGAL</span>
      </div>
      <address class="contact">
        <div>Level 9, 7 Ferris Lane</div>
        <div>Sydney NSW 2000</div>
        <div class="phone">02 8472 3159</div>
        <div>www.qvlegal.com.au</div>
      </address>
    </header>

    <p class="salutation">Dear Mr. Harlow,</p>

    <section class="letter-body">
      <p>Lorem ipsum dolor sit amet, consectetur adipiscing elit. Donec orci purus, luctus vitae dignissim eu, iaculis sed purus. Vivamus faucibus, ipsum nec aliquet viverra, leo mauris condimentum ligula, sit amet sagittis enim ligula quis arcu. Nam egestas tortor id nisi porttitor mattis. In tortor ante, ultricies in suscipit a, tempus non massa. Vivamus et auctor mi. Fusce vel massa nulla. Phasellus nec eros mauris, et scelerisque orci.</p>
      <p>Donec malesuada orci vitae nulla accumsan porta a id massa. Quisque accumsan iaculis magna sit amet fringilla. Maecenas consequat, magna eget tincidunt semper, odio nibh rutrum mi, id feugiat ante nisi eu risus. Vestibulum nunc orci, rhoncus a placerat in, ultricies in mi. Cras mattis varius eros, vel fringilla nisi suscipit eget. Quisque scelerisque sagittis nulla at porttitor.</p>
      <p>Sed id augue vitae urna euismod commodo aliquet a quam. Pellentesque arcu velit, cursus et malesuada ut, consequat et diam. Nullam erat sem, rhoncus id ullamcorper vitae, rhoncus et arcu. In ultricies ultricies nulla, ut rutrum nisi iaculis at. Donec eu magna a metus ornare faucibus. Fusce aliquet faucibus ultricies. Morbi semper, est id tincidunt gravida, sem arcu adipiscing lacus, ac bibendum nulla leo eu purus. Quisque nec diam sed risus consectetur accumsan quis quis nibh. Vestibulum id purus lorem.</p>
      <p>It is a long established fact that a reader will be distracted by the readable content of a page when looking at its layout. The point of using Lorem Ipsum is that it has a more-or-less normal distribution of letters, as opposed to using 'Content here, content here', making it look like readable English. Many desktop publishing packages</p>
    </section>

    <p class="closing">Sincerely,</p>

    <div class="signature" role="img" aria-label="Handwritten signature of James Harlow in blue ink"></div>
  </main>
</body>
</html>
```